Consulting company business cards

We have a base design, but would be willing to update. We have a new logo/"tag" that needs to be added. Current business card design is attached for reference into our "style."

Industry/Entity Type

Business

Contact Information for Business Card

Should contain name and title, office number, mobile number if appropriate, e-mail, website, physical address, and company logo.

Font styles to use
Other font styles liked:
• See current card design on KorvandBCard

Colors
0455a3
85acd3
aaaaaa

Requirements
Must have
• Our colors are navy blue, gray, and a lighter blue
Nice to have
• Design that I can easily drop in new names/titles as we hire employees.

```html
<!DOCTYPE html>
<html lang="en">
<head>
<meta charset="utf-8">
<title>Harlow business cards</title>
<link rel="stylesheet" href="https://fonts.googleapis.com/css2?family=Montserrat:wght@400;500;700;800&display=swap">
<style>
  :root {
    --navy: #0b3350;
    --navy-soft: #0f3d5d;
    --navy-text: #0e3a5a;
    --sky: #2aa8e0;
    --light-blue: #85acd3;
    --gray: #aaaaaa;
    --white: #ffffff;
    --stage: #e6e8eb;
  }
  * { margin: 0; padding: 0; box-sizing: border-box; }
  html, body { width: 1200px; height: 900px; overflow: hidden; }
  body {
    background: var(--stage);
    font-family: "Montserrat", Arial, sans-serif;
    display: flex; flex-direction: column; align-items: center; justify-content: center;
    gap: 40px;
  }
  .card {
    width: 700px; height: 400px; border-radius: 26px; position: relative; overflow: hidden;
    box-shadow: 0 6px 18px rgba(0,0,0,.18);
  }
  .card-front { background: var(--navy); color: var(--white); }
  .card-back { background: var(--white); color: var(--navy-text); }

  .front-decor {
    position: absolute; left: 200px; top: 40px; width: 300px; height: 300px;
    border-radius: 50%; background: var(--navy-soft);
  }

  .brand { position: absolute; }
  .brand-name {
    font-weight: 800; letter-spacing: 2px; line-height: 1; white-space: nowrap;
    display: flex; align-items: center; gap: 14px;
  }
  .brand-dot { border-radius: 50%; background: var(--light-blue); display: inline-block; flex: none; }
  .brand-tagline { font-weight: 500; letter-spacing: 2.5px; color: var(--gray); margin-top: 8px; white-space: nowrap; }

  .card-front .brand { left: 140px; top: 120px; }
  .card-front .brand-name { font-size: 80px; color: var(--white); }
  .card-front .brand-dot { width: 56px; height: 56px; }
  .card-front .brand-tagline { font-size: 16px; color: #8fa3b5; }
  .front-web {
    position: absolute; left: 0; right: 0; bottom: 52px; text-align: center;
    font-size: 22px; font-weight: 500; letter-spacing: 1px;
  }
  .front-web strong { font-weight: 700; }

  .card-back .brand { left: 48px; top: 160px; }
  .card-back .brand-name { font-size: 50px; color: var(--navy-text); gap: 10px; }
  .card-back .brand-dot { width: 36px; height: 36px; }
  .card-back .brand-tagline { font-size: 10px; letter-spacing: 2px; margin-top: 6px; }

  .divider { position: absolute; left: 400px; top: 70px; width: 1.5px; height: 250px; background: linear-gradient(var(--gray), rgba(170,170,170,0)); }

  .contact { position: absolute; left: 424px; top: 70px; font-size: 15px; line-height: 1.35; }
  .person-name { color: var(--sky); font-weight: 700; font-size: 23px; letter-spacing: 1px; line-height: 1.1; }
  .person-title { font-size: 15px; letter-spacing: 1px; margin-bottom: 16px; }
  .address { margin-bottom: 14px; }
  .contact-list { list-style: none; }
  .contact-list li { display: flex; align-items: center; gap: 10px; }
  .contact-list svg { width: 12px; height: 12px; flex: none; }
  .contact-list .web strong { color: var(--sky); font-weight: 700; }
</style>
</head>
<body>
  <section class="card card-front">
    <div class="front-decor" role="img" aria-label="Faint large brand emblem in the background"></div>
    <div class="brand">
      <div class="brand-name">HARLOW <span class="brand-dot"></span></div>
      <div class="brand-tagline">A CLOUD CONSULTING COMPANY</div>
    </div>
    <div class="front-web">www.<strong>HARLOWTECH</strong>.com</div>
  </section>

  <section class="card card-back">
    <div class="brand">
      <div class="brand-name">HARLOW <span class="brand-dot"></span></div>
      <div class="brand-tagline">A CLOUD CONSULTING COMPANY</div>
    </div>
    <div class="divider"></div>
    <div class="contact">
      <div class="person-name">NADIA KORVAND</div>
      <div class="person-title">OFFICE MANAGER</div>
      <div class="address">1780 w 48th st<br>brookfield ohio 44403</div>
      <ul class="contact-list">
        <li><svg viewBox="0 0 12 12"><path d="M2 1l2 0 1 3-1.3 1a7 7 0 003.3 3.3L8 7l3 1v2a1 1 0 01-1 1A9 9 0 011 2a1 1 0 011-1z" fill="var(--sky)"/></svg>555.014.2910</li>
        <li><svg viewBox="0 0 12 12"><rect x="3" y="0.5" width="6" height="11" rx="1.2" fill="var(--sky)"/></svg>555.014.2971</li>
        <li><svg viewBox="0 0 12 12"><rect x="0.8" y="2.5" width="10.4" height="7" rx="1" fill="none" stroke="var(--sky)" stroke-width="1.2"/><path d="M1 3l5 3.5L11 3" fill="none" stroke="var(--sky)" stroke-width="1.2"/></svg>nkorvand@harlowtech.com</li>
        <li class="web"><svg viewBox="0 0 12 12"><circle cx="6" cy="6" r="5" fill="none" stroke="var(--sky)" stroke-width="1.2"/><path d="M1 6h10M6 1c-2.5 3-2.5 7 0 10M6 1c2.5 3 2.5 7 0 10" fill="none" stroke="var(--sky)" stroke-width="1"/></svg><span>www.<strong>HARLOWTECH</strong>.com</span></li>
      </ul>
    </div>
  </section>
</body>
</html>
```